IT Company that provides secure IT solutions and services to our customers

We need business cards and a logo for a new IT Solutions company just created based in Kuala Lumpur, Malaysia. But will also be serving other countries in the region. We provide secure data, voice solutions on mobile platforms. Our first offering is encrypted voice and data solutions for IOS, Android, Windows and BlackBerry devices.

Target Market(s)

large organizations Govt, Police, Defence, Anti-corruption, Legal, highly regulated industries such as Health-care, Financial, Banking, Insurance,

Industry/Entity Type

Information Technology

Contact Information for Business Card

VelmoraNet (Logo - colour is ORVEX blue)Roshan Adeel Managing Director Velmora Net Sdn. Bhd.5th Floor, Block D, Wisma PLB,No.14 Jalan Seri Melor,50470, Kuala LumpurMalaysia

Font styles to use
Sans Serif

Colors
3176b5
ec1f27
fbed22

Requirements
Must have
• VelmoraNet all in Blue like ORVEX blue. A logo design perhaps a play of VN, K with a dangling T (colour can be any)
Nice to have
• I want a clean crisp card, not too busy, easy to read.

```html
<!DOCTYPE html>
<html lang="en">
<head>
<meta charset="utf-8">
<title>VelmoraNet Business Card</title>
<link rel="stylesheet" href="https://fonts.googleapis.com/css2?family=Source+Sans+3:wght@400;600;700&display=swap">
<style>
  :root {
    --canvas: #000000;
    --card: #323336;
    --brand-blue: #1f60b5;
    --text-light: #e6e6e6;
    --divider: #45464a;
  }
  * { margin: 0; padding: 0; box-sizing: border-box; }
  html, body { width: 1200px; height: 900px; overflow: hidden; background: var(--canvas); }
  body { position: relative; font-family: "Source Sans 3", "Myriad Pro", sans-serif; }

  .card {
    position: absolute;
    top: 270px;
    width: 458px;
    height: 283px;
    background: var(--card);
    border-radius: 14px;
  }
  .card--front { left: 137px; }
  .card--back { left: 626px; }

  .front-mark {
    position: absolute;
    left: 48px;
    top: 92px;
    width: 104px;
    display: flex;
    flex-direction: column;
    align-items: center;
    gap: 10px;
  }
  .mark-square {
    width: 60px;
    height: 60px;
    border: 3px solid var(--brand-blue);
  }
  .front-mark .brand-name {
    font-size: 19px;
    font-weight: 700;
    color: var(--brand-blue);
    line-height: 1;
  }

  .divider {
    position: absolute;
    left: 190px;
    top: 93px;
    width: 1px;
    height: 97px;
    background: var(--divider);
  }

  .contact {
    position: absolute;
    left: 212px;
    top: 75px;
    color: var(--text-light);
    font-size: 13px;
    line-height: 16.5px;
  }
  .contact .person-name,
  .contact .company-name {
    color: var(--brand-blue);
    font-weight: 700;
    font-size: 14.5px;
  }
  .contact .company { margin-top: 31px; margin-left: 2px; }

  .back-logo {
    position: absolute;
    left: 61px;
    top: 109px;
    display: flex;
    align-items: center;
    gap: 22px;
  }
  .back-logo .mark-square { width: 64px; height: 64px; }
  .back-logo .brand-name {
    font-size: 50px;
    font-weight: 700;
    color: var(--brand-blue);
    line-height: 1;
    letter-spacing: 0.5px;
  }
</style>
</head>
<body>
  <section class="card card--front">
    <div class="front-mark">
      <div class="mark-square"></div>
      <span class="brand-name">VelmoraNet</span>
    </div>
    <div class="divider"></div>
    <div class="contact">
      <div class="person">
        <div class="person-name">Roshan Adeel</div>
        <div class="person-title">Managing Director</div>
      </div>
      <div class="company">
        <div class="company-name">Velmora Net</div>
        <address style="font-style: normal;">
          Sdn. Bhd.5th Floor, Block D,<br>
          Wisma PLB,No.14 Jalan Seri Melor,<br>
          50470, Kuala Lumpur<br>
          Malaysia
        </address>
      </div>
    </div>
  </section>

  <section class="card card--back">
    <div class="back-logo">
      <div class="mark-square"></div>
      <span class="brand-name">VelmoraNet</span>
    </div>
  </section>
</body>
</html>
```